Business Card for Coach - ready to print

Design Business Card ready to order prints www.lukasbrenner.coach

* An Overview / Background of the Business & Services
· Coaching
· Personal growth
* The Target Market / Audience you are trying to reach
· private person in different roles (self, familiy, business role)s
* Design Specifics; any preferences or ideas for Style, Colour, Imagery, etc
· See www.lukasbrenner.coach
· "simple" design
· (small) element of surprise / unusual element

* Information that will be placed in the Business Card
· Beratung und Coaching
· Address: Lukas Brenner, Mosering 42, CH-8312 Winterthur, Mobile +41 79 264 53 07
* Do you have an existing website or Facebook page where designers can learn more about your company?
· lukasbrenner.coach

Target Market(s)

private person in different roles (self, familiy, business role)

Industry/Entity Type

Life Coaching

Contact Information for Business Card

Lukas Brenner
Mosering 42
CH-8312 Winterthur

Mobile: +41 79 264 53 07
Email: lubr@alpimail.ch
www.lukasbrenner.coach

Font styles to use
Sans Serif

Colors

Designer to choose colors to be used in the design.

Requirements
Must have
• "simple" design
• element of surprise / unusual element
• Beratung & Coaching
• see www.lukasbrenner.coach for colors and so...
Nice to have
• TA Symbol (three rings on top of each other) - unsual presentation
• QR Code of Website (see if it fits in and still looks good).

```html
<!DOCTYPE html>
<html lang="de">
<head>
<meta charset="utf-8">
<title>Lukas Brenner – Business Card</title>
<link rel="stylesheet" href="https://fonts.googleapis.com/css2?family=Lato:wght@300;400;700;900&display=swap">
<style>
  :root {
    --stage: #e9eaec;
    --card-light: #ffffff;
    --card-dark: #4a4a4c;
    --ink: #111111;
    --ink-soft: #4d4d4d;
    --rule-light: #d4d4d4;
    --rule-dark: #6d6d70;
    --text-on-dark: #f2f2f2;
    --photo-top: #9a9ea3;
    --photo-bottom: #5f646b;
  }
  * { box-sizing: border-box; margin: 0; padding: 0; }
  html, body {
    width: 1200px; height: 900px; overflow: hidden;
    background: var(--stage);
    font-family: "Lato", sans-serif;
  }
  .canvas { position: relative; width: 1200px; height: 900px; }
  .card {
    position: absolute; left: 250px; width: 700px; height: 400px;
    border-radius: 28px;
    box-shadow: 0 6px 18px rgba(0,0,0,0.12);
  }
  .card--front { top: 40px; background: var(--card-light); }
  .card--back  { top: 465px; background: var(--card-dark); }

  .portrait {
    position: absolute; left: 66px; top: 110px;
    width: 180px; height: 180px; border-radius: 50%;
    background: linear-gradient(160deg, var(--photo-top), var(--photo-bottom));
    border: 2px solid #2b2b2b;
  }
  .divider {
    position: absolute; left: 292px; top: 70px;
    width: 1px; height: 260px; background: var(--rule-light);
  }
  .details { position: absolute; left: 326px; top: 70px; color: var(--ink); }
  .details__name { font-weight: 900; font-size: 38px; letter-spacing: 0.5px; line-height: 1; }
  .details__role { font-weight: 400; font-size: 20px; color: var(--ink-soft); margin-top: 6px; }
  .details__company { font-weight: 700; font-size: 20px; margin-top: 10px; }
  .details__address { font-size: 20px; color: var(--ink-soft); line-height: 1.25; }
  .contact { list-style: none; margin-top: 12px; font-size: 20px; color: var(--ink-soft); line-height: 1.3; }
  .contact li { display: flex; align-items: center; gap: 10px; }
  .contact svg { width: 18px; height: 18px; flex: none; }

  .services {
    position: absolute; inset: 0;
    display: flex; flex-direction: column; align-items: center; justify-content: center;
    color: var(--text-on-dark); text-align: center;
  }
  .services__title { font-weight: 900; font-size: 32px; letter-spacing: 1px; }
  .services__rule { width: 150px; height: 1px; background: var(--rule-dark); margin: 12px 0 10px; }
  .services__item { font-weight: 300; font-size: 26px; line-height: 1.25; }
</style>
</head>
<body>
<main class="canvas">
  <section class="card card--front" aria-label="Visitenkarte Vorderseite">
    <div class="portrait" role="img" aria-label="Porträtfoto von Lukas Brenner"></div>
    <div class="divider"></div>
    <div class="details">
      <h1 class="details__name">LUKAS BRENNER</h1>
      <p class="details__role">Founder &amp; CEO</p>
      <p class="details__company">Beratung and Coaching</p>
      <p class="details__address">Lukas Brenner, Mosering 42<br>CH-8312 Winterthur</p>
      <ul class="contact">
        <li>
          <svg viewBox="0 0 20 20" aria-hidden="true"><circle cx="10" cy="10" r="9.5" fill="#222"/><path d="M7 5.5l1.6 0.4 0.5 2.2-1 0.8a6 6 0 0 0 3 3l0.8-1 2.2 0.5 0.4 1.6c-0.4 0.9-1.4 1.4-2.4 1.2A8 8 0 0 1 5.8 7.9C5.6 6.9 6.1 5.9 7 5.5z" fill="#fff"/></svg>
          +41 79 264 53 07
        </li>
        <li>
          <svg viewBox="0 0 20 20" aria-hidden="true"><rect x="1" y="3" width="18" height="14" rx="1.5" fill="#222"/><path d="M2 4.5l8 6.5 8-6.5M2 16l6-5.5M18 16l-6-5.5" stroke="#fff" stroke-width="1.3" fill="none"/></svg>
          lubr@alpimail.ch
        </li>
        <li>
          <svg viewBox="0 0 20 20" aria-hidden="true"><circle cx="10" cy="10" r="9.5" fill="#222"/><g stroke="#fff" stroke-width="1.1" fill="none"><circle cx="10" cy="10" r="7"/><ellipse cx="10" cy="10" rx="3" ry="7"/><path d="M3 10h14M4.2 6.5h11.6M4.2 13.5h11.6"/></g></svg>
          www.lukasbrenner.coach
        </li>
      </ul>
    </div>
  </section>

  <section class="card card--back" aria-label="Visitenkarte Rückseite">
    <div class="services">
      <h2 class="services__title">SERVIES:</h2>
      <div class="services__rule"></div>
      <p class="services__item">Coaching</p>
      <p class="services__item">Personal growth</p>
    </div>
  </section>
</main>
</body>
</html>
```